Company identity deisgn should support 2 languages

I would like to get our company identity design
This includes the following only
Business Cards 2 languages Arabic and English
Email signature
Letterhead
Linkedin profile images
Attached is the logo in Ai format

Requirements
Must have
• For business card
Must have
Name and Adrees in arabic
Name and Address in english
You might use both side of the card
Should not have
• Any pictures other than the logo

```html
<!DOCTYPE html>
<html lang="en">
<head>
<meta charset="utf-8">
<title>Novamind Systems – Business Card</title>
<link href="https://fonts.googleapis.com/css2?family=Figtree:wght@400;500;700;800&family=Noto+Naskh+Arabic:wght@400;700&display=swap" rel="stylesheet">
<style>
:root{
  --page:#e9eaec;
  --card:#ffffff;
  --brand-blue:#1076bf;
  --swoosh-grey:#b3b5ba;
  --text-on-blue:#ffffff;
  --text-grey:#6d6f73;
}
*{margin:0;padding:0;box-sizing:border-box}
html,body{width:1200px;height:1200px;overflow:hidden;background:var(--page)}
body{font-family:"Figtree",Arial,sans-serif;position:relative}
.card{position:absolute;left:150px;width:900px;height:514px;background:var(--card);border-radius:34px;overflow:hidden;box-shadow:0 10px 24px rgba(0,0,0,.18)}
.card--english{top:46px}
.card--arabic{top:640px}
.card__shape{position:absolute;inset:0;width:100%;height:100%}
.brand{position:absolute;left:398px;top:100px;display:flex;align-items:center;gap:14px}
.brand__dot{width:30px;height:30px;border-radius:50%;background:var(--brand-blue)}
.brand__name{font-weight:700;font-size:34px;letter-spacing:1px;color:var(--brand-blue);text-transform:uppercase}
.details{position:absolute;left:42px;top:242px;color:var(--text-on-blue)}
.details__name{font-weight:800;font-size:28px;letter-spacing:.3px;line-height:1.1}
.details__title{font-size:19px;margin-top:4px}
.details__address{font-size:19px;line-height:26px;margin-top:14px}
.contacts{list-style:none;margin-top:14px;font-size:19px;line-height:26px}
.contacts li{display:flex;align-items:center;gap:12px}
.contacts svg{width:16px;height:16px;fill:var(--text-on-blue);flex:none}
.card--arabic .details__name,.card--arabic .details__title,.card--arabic .details__address{font-family:"Noto Naskh Arabic","Figtree",serif}
.card--arabic .details__name{font-size:28px;font-weight:700}
.card--arabic .details__title{font-size:20px;font-weight:700;margin-top:-4px}
.card--arabic .details__address{font-size:18px;line-height:30px;margin-top:6px}
</style>
</head>
<body>

<section class="card card--english" aria-label="Business card, English side">
  <svg class="card__shape" viewBox="0 0 800 457" preserveAspectRatio="none" aria-hidden="true">
    <path d="M100 0 C110 90 210 160 318 232 C420 300 472 370 468 457 L462 457 C468 360 400 290 300 220 C200 150 110 80 100 0 Z" fill="var(--swoosh-grey)"/>
    <path d="M0 0 H100 C106 80 200 150 300 220 C400 290 468 360 462 457 H0 Z" fill="var(--brand-blue)"/>
  </svg>
  <div class="brand"><span class="brand__dot"></span><span class="brand__name">Novamind Systems</span></div>
  <div class="details">
    <h1 class="details__name">DANIEL HART</h1>
    <p class="details__title">President</p>
    <p class="details__address">4120 Willow Court<br>Juneau, Alaska 99801</p>
    <ul class="contacts">
      <li><svg viewBox="0 0 16 16"><path d="M3 1l3 3-2 2c1 2 3 4 5 5l2-2 3 3-2 3C6 15 1 10 0 3z"/></svg>555-214-0187</li>
      <li><svg viewBox="0 0 16 16"><path d="M4 0h8a1 1 0 011 1v14a1 1 0 01-1 1H4a1 1 0 01-1-1V1a1 1 0 011-1zm1 2v10h6V2z"/></svg>555-608-3321</li>
      <li><svg viewBox="0 0 16 16"><path d="M1 4h14v9H1zm1 1l6 4 6-4z"/></svg>hello@novamindsystems.com</li>
      <li><svg viewBox="0 0 16 16"><path d="M8 1a7 7 0 100 14A7 7 0 008 1zm-3 4l3 1 1 3-2 1-1 3-1-3-2-1z"/></svg>www.novamindsystems.com</li>
    </ul>
  </div>
</section>

<section class="card card--arabic" aria-label="Business card, Arabic side">
  <svg class="card__shape" viewBox="0 0 800 457" preserveAspectRatio="none" aria-hidden="true">
    <path d="M100 0 C110 90 210 160 318 232 C420 300 472 370 468 457 L462 457 C468 360 400 290 300 220 C200 150 110 80 100 0 Z" fill="var(--swoosh-grey)"/>
    <path d="M0 0 H100 C106 80 200 150 300 220 C400 290 468 360 462 457 H0 Z" fill="var(--brand-blue)"/>
  </svg>
  <div class="brand"><span class="brand__dot"></span><span class="brand__name">Novamind Systems</span></div>
  <div class="details">
    <h1 class="details__name" lang="ar" dir="rtl">دانيال هارت</h1>
    <p class="details__title" lang="ar" dir="rtl" style="text-align:left">رئيس</p>
    <p class="details__address" lang="ar">4120 ويلو كورت<br>جونو ، ألاسكا 99801</p>
    <ul class="contacts">
      <li><svg viewBox="0 0 16 16"><path d="M3 1l3 3-2 2c1 2 3 4 5 5l2-2 3 3-2 3C6 15 1 10 0 3z"/></svg>555-214-0187</li>
      <li><svg viewBox="0 0 16 16"><path d="M4 0h8a1 1 0 011 1v14a1 1 0 01-1 1H4a1 1 0 01-1-1V1a1 1 0 011-1zm1 2v10h6V2z"/></svg>555-608-3321</li>
      <li><svg viewBox="0 0 16 16"><path d="M1 4h14v9H1zm1 1l6 4 6-4z"/></svg>hello@novamindsystems.com</li>
      <li><svg viewBox="0 0 16 16"><path d="M8 1a7 7 0 100 14A7 7 0 008 1zm-3 4l3 1 1 3-2 1-1 3-1-3-2-1z"/></svg>www.novamindsystems.com</li>
    </ul>
  </div>
</section>

</body>
</html>
```